Buch-/eBook-Cover für Traumatherapeutin
Zielgruppe
Ich bin Traumatherapeutin und schreibe ein Buch zum Thema Trauma bearbeiten.
Meine Zielgruppe sucht Heilung, Genesung, Selbstliebe etc.
Aufgabenstellung
Buchcover
Bitte erstell mir ein modernes positives inspirierendes Buchcover mit dem
Titel: 'Morgenlicht NEU entdecken“
Untertitel: „Spüre den Mut der ganz in dir wohnt“
Dr. Mira Kessow
Ich hätte gerne ein modernes Buch, das entweder einen Bezug zum Thema Trauma hat oder aber einfach stylische Schriftzüge. Bin aber auch offen für andere Vorschläge.
Dunkelblau, weiß und türkis oder auch rosa mag ich ganz gerne. Wobei Dunkelblau, weiß und türkis meine Favoriten sind und mit rosa höchstens kleinere Akzente gesetzt werden sollten.
Das Buchcover soll modern sein und direkt ansprechen. Gerne eine originelle Lösung, oder etwas Besonderes, etwas das Tiefe ausdrückt, oder man mehrmals hinsehen muss um etwas zu erkennen oder etwas das mehr Interpretationsspielraum lässt.
Gerne auch viel weiß, zumindest heller und nicht zu dunkel. Stylish, aber nicht überfrachtet.
Schreib mich gerne an, wenn du Fragen hast.
Ich habe mal zwei Beispiel von Typolösungen angehängt, die ich ganz cool fände.
Ich freue mich auf deine Ideen :-)
Ganz liebe Grüße
Mira

```html
<!DOCTYPE html>
<html lang="de">
<head>
<meta charset="utf-8">
<title>Morgenlicht NEU entdecken – Buchcover</title>
<link rel="stylesheet" href="https://fonts.googleapis.com/css2?family=Anton&family=Lexend:wght@500&family=Montserrat:wght@700&display=swap">
<style>
  :root {
    --stage: #8f8f8f;
    --teal: #45c1b8;
    --teal-deep: #3bb5ac;
    --teal-light: #9fe0dc;
    --white: #ffffff;
    --navy: #1f3560;
    --figure-light: #e3e7ea;
    --figure-dark: #6d7480;
  }
  * { margin: 0; padding: 0; box-sizing: border-box; }
  html, body {
    width: 668px; height: 1200px; overflow: hidden;
    background: var(--stage);
  }
  .cover {
    position: absolute; left: 34px; top: 151px;
    width: 600px; height: 898px; overflow: hidden;
    background:
      radial-gradient(circle at 6% 2%, rgba(210,245,250,.85) 0, rgba(210,245,250,0) 150px),
      radial-gradient(ellipse at 15% 68%, rgba(255,255,255,.55) 0, rgba(255,255,255,0) 260px),
      linear-gradient(180deg, var(--teal) 0%, var(--teal-deep) 100%);
    box-shadow: 4px 6px 10px rgba(0,0,0,.3);
  }
  .cover__glow {
    position: absolute; left: -40px; top: 480px; width: 420px; height: 260px;
    background: linear-gradient(160deg, rgba(255,255,255,0) 20%, rgba(255,255,255,.35) 50%, rgba(255,255,255,0) 80%);
    transform: rotate(-8deg);
  }
  .cover__spark {
    position: absolute; left: 452px; top: 586px; width: 14px; height: 14px; border-radius: 50%;
    background: rgba(255,255,255,.8); box-shadow: 0 0 10px rgba(255,255,255,.9);
  }
  .title {
    position: absolute; left: 0; top: 28px; width: 100%;
    text-align: center; color: var(--white);
    font-family: 'Anton', sans-serif; text-transform: uppercase;
    text-shadow: 0 4px 8px rgba(0,40,40,.25);
  }
  .title__line { display: block; line-height: 1; }
  .title__line--top { font-size: 92px; letter-spacing: 1px; }
  .title__line--big { font-size: 200px; line-height: .86; margin-top: 4px; letter-spacing: 3px; }
  .title__line--bottom { font-size: 104px; margin-top: 2px; letter-spacing: 1px; }
  .subtitle {
    position: absolute; left: 0; top: 428px; width: 100%;
    text-align: center; color: var(--white);
    font-family: 'Lexend', sans-serif; font-weight: 500; font-size: 31px; line-height: 1.4;
  }
  .arch {
    position: absolute; left: 171px; top: 512px; width: 256px; height: 330px;
    background: linear-gradient(180deg, var(--white) 0%, #f3f6f6 100%);
    border-radius: 128px 128px 0 0;
  }
  .arch__figure {
    position: absolute; left: 98px; top: 40px; width: 60px; height: 250px;
    border-radius: 30px 30px 6px 6px;
    background: linear-gradient(180deg, var(--figure-dark) 0%, var(--figure-dark) 40%, var(--figure-light) 55%, var(--figure-dark) 100%);
  }
  .arch__beam {
    position: absolute; left: 70px; bottom: 0; width: 90px; height: 60px;
    background: linear-gradient(0deg, rgba(69,193,184,.6), rgba(69,193,184,0));
    clip-path: polygon(0 100%, 100% 100%, 70% 0, 55% 0);
  }
  .author-band {
    position: absolute; left: 0; bottom: 0; width: 100%; height: 75px;
    background: var(--white);
    display: flex; align-items: center; justify-content: center;
  }
  .author {
    font-family: 'Montserrat', sans-serif; font-weight: 700; font-size: 26px;
    letter-spacing: 3px; color: var(--navy); text-transform: uppercase;
  }
</style>
</head>
<body>
  <main class="cover">
    <div class="cover__glow"></div>
    <div class="cover__spark"></div>
    <h1 class="title">
      <span class="title__line title__line--top">Morgenlicht</span>
      <span class="title__line title__line--big">Neu</span>
      <span class="title__line title__line--bottom">Entdecken</span>
    </h1>
    <p class="subtitle">Spüre den Mut<br>der ganz in dir wohnt</p>
    <div class="arch">
      <div class="arch__figure" role="img" aria-label="Person von hinten mit erhobenen Armen, die ins Licht schwebt"></div>
      <div class="arch__beam"></div>
    </div>
    <footer class="author-band">
      <p class="author">Dr. Mira Kessow</p>
    </footer>
  </main>
</body>
</html>
```